German Headhunter/ HR Consultancy needs Business Cards Design

We need a business Card Design for our Company in Stuttgart. We are specialized as Headhunter/ HR Consultancy in Placement of specialist and managers in permanent employment. Please refer to our business logo.

```html
<!DOCTYPE html>
<html lang="de">
<head>
<meta charset="utf-8">
<title>Vertex Personalberatung – Visitenkarte</title>
<link href="https://fonts.googleapis.com/css2?family=Montserrat:wght@600;700&family=Arimo:wght@400;700&display=swap" rel="stylesheet">
<style>
  :root {
    --page: #e9e9ea;
    --card: #2f3033;
    --card-deep: #262729;
    --blue: #3551b8;
    --white: #ffffff;
    --grey: #8d8e92;
    --faint: #38393c;
  }
  * { box-sizing: border-box; margin: 0; padding: 0; }
  html, body { width: 1200px; height: 802px; overflow: hidden; background: var(--page); }
  .sheet { position: relative; width: 1200px; height: 802px; }

  .card {
    position: absolute; top: 246px; width: 540px; height: 309px;
    background: var(--card); overflow: hidden;
    font-family: "Arimo", Arial, sans-serif;
  }
  .card--front { left: 45px; }
  .card--back { left: 615px; }

  /* front */
  .front__watermark {
    position: absolute; right: 70px; top: -30px; width: 200px; height: 200px;
    background: var(--faint);
  }
  .brand { position: absolute; display: flex; align-items: center; gap: 12px; }
  .brand__square { width: 22px; height: 22px; background: var(--blue); flex: none; }
  .brand__name {
    font-family: "Montserrat", Arial, sans-serif; font-weight: 700;
    color: var(--white); letter-spacing: .5px; line-height: 1.1;
  }
  .front__brand { left: 38px; top: 44px; }
  .front__brand .brand__name { font-size: 15px; }

  .person { position: absolute; left: 90px; top: 118px; }
  .person__name { color: var(--blue); font-weight: 700; font-size: 17px; letter-spacing: .5px; }
  .person__role { color: var(--grey); font-size: 13px; margin-top: 3px; }

  .contacts { position: absolute; left: 90px; top: 182px; list-style: none; }
  .contacts li { display: flex; align-items: center; gap: 9px; color: var(--white); font-size: 14px; height: 22px; }
  .contacts svg { width: 12px; height: 12px; fill: var(--grey); flex: none; }

  .edge-tab { position: absolute; left: 0; top: 190px; width: 7px; height: 40px; background: var(--blue); }

  .address {
    position: absolute; right: 30px; top: 200px; text-align: right;
    color: var(--white); font-size: 13px; line-height: 1.35;
  }
  .band { position: absolute; left: 0; bottom: 0; height: 10px; width: 100%; display: flex; }
  .band__blue { width: 56%; background: var(--blue); }
  .band__white { flex: 1; background: var(--white); }

  /* back */
  .back__mark {
    position: absolute; right: 40px; top: 30px; width: 190px; height: 190px;
    background: linear-gradient(135deg, #1e1f21, #3b3c3f 70%, #5a5b5e);
  }
  .back__brand { left: 60px; top: 205px; }
  .back__brand .brand__name { font-size: 22px; }
  .back__brand .brand__square { width: 28px; height: 28px; }
</style>
</head>
<body>
<main class="sheet">

  <section class="card card--front" aria-label="Vorderseite">
    <div class="front__watermark"></div>
    <div class="brand front__brand">
      <span class="brand__square"></span>
      <span class="brand__name">VERTEX<br>PERSONALBERATUNG</span>
    </div>
    <div class="person">
      <p class="person__name">LUKAS BERGER</p>
      <p class="person__role">Manager</p>
    </div>
    <span class="edge-tab"></span>
    <ul class="contacts">
      <li><svg viewBox="0 0 24 24"><path d="M6.6 10.8a15 15 0 0 0 6.6 6.6l2.2-2.2a1 1 0 0 1 1-.25 11.4 11.4 0 0 0 3.6.57 1 1 0 0 1 1 1V20a1 1 0 0 1-1 1A17 17 0 0 1 3 4a1 1 0 0 1 1-1h3.5a1 1 0 0 1 1 1c0 1.25.2 2.45.57 3.57a1 1 0 0 1-.25 1z"/></svg>123-456-2100</li>
      <li><svg viewBox="0 0 24 24"><path d="M2 5h20v14H2z M2 5l10 8 10-8" /></svg>youremail@mailbox.com</li>
      <li><svg viewBox="0 0 24 24"><circle cx="12" cy="12" r="10"/></svg>www.yourwebsite.com</li>
    </ul>
    <p class="address">Your address<br>city, state, ZIP 0000</p>
    <div class="band"><span class="band__blue"></span><span class="band__white"></span></div>
  </section>

  <section class="card card--back" aria-label="Rückseite">
    <div class="back__mark"></div>
    <div class="brand back__brand">
      <span class="brand__square"></span>
      <span class="brand__name">VERTEX<br>PERSONALBERATUNG</span>
    </div>
  </section>

</main>
</body>
</html>
```